Harbor Crestline (Business Card Design)

Need business cards designed. Something modern, chic, and sleek. Mabye the back of the card should be the navy blue that is in the logo and then just the logo on the back.

Target Market(s)

Those in the hotel, office, and renovation industry

Contact Information for Business Card

1. Logo 2. Dorian Fenwick 3. CEO/Founder 4. Phone: (833) HarbCre / (833) 427-2731 5. Email: dorian@theharborcrestline.com 6. Website: www.theharborcrestline.com

Font styles to use
Other font styles liked:
• Look at the logo font and base the font for everything else off of that.

Colors
0054AA
0677BA
7BADD7
CADEEF
E8F1F8

Requirements
Must have
• Colors that are associated in the logo
Nice to have
• Sleek modern clean and chic design.

```html
<!DOCTYPE html>
<html lang="en">
<head>
<meta charset="utf-8">
<title>Harbor Crestline – Business Card</title>
<link rel="stylesheet" href="https://fonts.googleapis.com/css2?family=Montserrat:wght@600;700&family=Open+Sans:wght@400;600&display=swap">
<style>
  :root {
    --navy: #101d4f;
    --navy-deep: #0b1540;
    --gold: #c79f45;
    --paper: #f5f5f5;
    --ink: #1b1b1b;
    --backdrop: #2a2a2c;
  }
  * { box-sizing: border-box; margin: 0; padding: 0; }
  html, body { width: 1200px; height: 780px; overflow: hidden; }
  body {
    background: var(--backdrop);
    display: flex;
    align-items: center;
    justify-content: center;
    gap: 40px;
    font-family: "Open Sans", Arial, sans-serif;
  }
  .card {
    position: relative;
    width: 550px;
    height: 314px;
    border-radius: 4px;
    overflow: hidden;
    box-shadow: 0 10px 30px rgba(0,0,0,.45);
  }

  /* Front */
  .card-front { background: var(--paper); }
  .brand {
    position: absolute;
    left: 38px; top: 78px;
    width: 190px;
    display: flex; align-items: center; gap: 12px;
  }
  .brand-mark { width: 22px; height: 22px; background: var(--navy); flex: none; }
  .brand-name {
    font-family: "Montserrat", Arial, sans-serif;
    font-weight: 700;
    font-size: 23px;
    line-height: 1.1;
    letter-spacing: 1.5px;
    color: var(--navy);
    text-transform: uppercase;
  }
  .divider {
    position: absolute;
    left: 242px; top: 60px;
    width: 1px; height: 135px;
    background: var(--navy);
    transform: rotate(18deg);
    transform-origin: top;
  }
  .person { position: absolute; left: 270px; top: 54px; }
  .person-name {
    font-family: "Montserrat", Arial, sans-serif;
    font-weight: 700;
    font-size: 30px;
    line-height: 1;
  }
  .person-name .first { color: var(--gold); }
  .person-name .last { color: var(--navy); }
  .person-title { font-size: 14px; color: var(--ink); margin-top: 4px; }
  .contacts { list-style: none; margin-top: 14px; }
  .contacts li {
    display: flex; align-items: center; gap: 8px;
    font-size: 12.5px; color: var(--ink); line-height: 22px;
  }
  .contacts svg { width: 13px; height: 13px; flex: none; fill: var(--gold); }
  .address-band {
    position: absolute;
    left: 0; bottom: 28px;
    width: 450px; height: 32px;
    background: var(--gold);
    color: #fff;
    font-size: 13px;
    line-height: 32px;
    padding-left: 34px;
  }
  .corner-block {
    position: absolute;
    right: 0; bottom: 0;
    width: 100px; height: 60px;
    background: var(--navy);
    display: flex; align-items: center; justify-content: center;
  }
  .corner-square { width: 22px; height: 22px; background: #fff; }

  /* Back */
  .card-back {
    background: var(--navy);
    display: flex; align-items: center; justify-content: center;
  }
  .back-texture {
    position: absolute; inset: 0;
    background: linear-gradient(120deg, var(--navy-deep) 0%, var(--navy) 55%, #3b4a86 100%);
  }
  .back-brand {
    position: relative;
    display: flex; align-items: center; gap: 16px;
  }
  .back-brand .brand-mark { width: 30px; height: 30px; background: #fff; }
  .back-brand .brand-name { color: #fff; font-size: 34px; letter-spacing: 3px; }
</style>
</head>
<body>

  <section class="card card-front">
    <div class="brand">
      <span class="brand-mark"></span>
      <span class="brand-name">Harbor Crestline</span>
    </div>
    <span class="divider"></span>

    <div class="person">
      <h1 class="person-name"><span class="first">Dorian</span> <span class="last">Fenwick</span></h1>
      <p class="person-title">CEO/Founder</p>
      <ul class="contacts">
        <li>
          <svg viewBox="0 0 24 24"><path d="M6.6 10.8a15.1 15.1 0 0 0 6.6 6.6l2.2-2.2a1 1 0 0 1 1-.25 11.4 11.4 0 0 0 3.6.57 1 1 0 0 1 1 1V20a1 1 0 0 1-1 1A17 17 0 0 1 3 4a1 1 0 0 1 1-1h3.5a1 1 0 0 1 1 1c0 1.25.2 2.45.57 3.57a1 1 0 0 1-.25 1z"/></svg>
          (833) HarbCre / (833) 427-2731
        </li>
        <li>
          <svg viewBox="0 0 24 24"><path d="M12 2a10 10 0 1 0 0 20 10 10 0 0 0 0-20zm6.9 6h-2.9a15.6 15.6 0 0 0-1.4-3.6A8 8 0 0 1 18.9 8zM12 4a14 14 0 0 1 1.9 4h-3.8A14 14 0 0 1 12 4zM4.3 14a8 8 0 0 1 0-4h3.4a16.5 16.5 0 0 0 0 4zm.8 2h2.9a15.6 15.6 0 0 0 1.4 3.6A8 8 0 0 1 5.1 16zM8 8H5.1a8 8 0 0 1 4.3-3.6A15.6 15.6 0 0 0 8 8zm4 12a14 14 0 0 1-1.9-4h3.8A14 14 0 0 1 12 20zm2.3-6H9.7a14.7 14.7 0 0 1 0-4h4.6a14.7 14.7 0 0 1 0 4zm.3 5.6A15.6 15.6 0 0 0 16 16h2.9a8 8 0 0 1-4.3 3.6zM16.3 14a16.5 16.5 0 0 0 0-4h3.4a8 8 0 0 1 0 4z"/></svg>
          www.theharborcrestline.com
        </li>
        <li>
          <svg viewBox="0 0 24 24"><path d="M3 5h18a1 1 0 0 1 1 1v12a1 1 0 0 1-1 1H3a1 1 0 0 1-1-1V6a1 1 0 0 1 1-1zm1 2.2V17h16V7.2l-8 5.3z M5 7l7 4.6L19 7z"/></svg>
          dorian@theharborcrestline.com
        </li>
      </ul>
    </div>

    <p class="address-band">4120 Meridian Ave Suite 210, Fairhaven, MD 21090</p>
    <div class="corner-block"><span class="corner-square"></span></div>
  </section>

  <section class="card card-back">
    <div class="back-texture" role="img" aria-label="Repeating brand pattern across the navy background"></div>
    <div class="back-brand">
      <span class="brand-mark"></span>
      <span class="brand-name">Harbor Crestline</span>
    </div>
  </section>

</body>
</html>
```